Redesign of business card for Cedar Ridge Mechanical

We are looking for a new design for our business cards for Cedar Ridge Mechanical. We are a plumbing & HVAC construction company, operating on the West Coast of Canada and USA. Logo attached.
Industry/Entity Type
Construction - Plumbing & HVAC
Contact Information for Business Card
Name, address, phone numbers, email, website address
Look and feel
Each slider illustrates characteristics of the customer's brand and the style your logo design should communicate.

```html
<!DOCTYPE html>
<html lang="en">
<head>
<meta charset="utf-8">
<title>Cedar Ridge Mechanical – Business Card</title>
<link href="https://fonts.googleapis.com/css2?family=Quicksand:wght@500;600;700&display=swap" rel="stylesheet">
<style>
  :root {
    --page-bg: #d9d3ca;
    --card-bg: #ece8e1;
    --card-edge: #f6f3ee;
    --ink: #1b1b1b;
    --ink-soft: #3c3c3c;
    --band: #121212;
    --band-text: #e9e6e1;
  }
  * { box-sizing: border-box; margin: 0; padding: 0; }
  html, body {
    width: 1200px; height: 1047px; overflow: hidden;
    background: var(--page-bg);
    font-family: "Quicksand", sans-serif;
  }
  .business-card {
    position: absolute; left: 100px; top: 253px;
    width: 1000px; height: 540px;
    background: var(--card-bg);
    border: 2px solid var(--card-edge);
    border-radius: 24px;
    overflow: hidden;
  }
  .brand-lockup {
    position: absolute; left: 120px; top: 160px; width: 410px;
    display: flex; flex-direction: column; align-items: center; gap: 22px;
  }
  .brand-square {
    width: 70px; height: 70px; background: var(--ink); border-radius: 6px;
  }
  .brand-name {
    font-weight: 700; font-size: 38px; line-height: 1.15;
    color: var(--ink); text-align: center; text-transform: uppercase; letter-spacing: 1px;
  }
  .divider {
    position: absolute; left: 563px; top: 120px;
    width: 2px; height: 302px; background: var(--ink);
  }
  .contact-block { position: absolute; left: 590px; top: 118px; color: var(--ink); }
  .person-name { font-weight: 700; font-size: 33px; letter-spacing: 0.5px; }
  .person-title { font-weight: 500; font-size: 25px; color: var(--ink-soft); margin-top: 8px; }
  .address { font-weight: 600; font-size: 25px; line-height: 37px; margin-top: 26px; }
  .contact-list { list-style: none; margin-top: 24px; }
  .contact-list li {
    display: flex; align-items: center; gap: 10px;
    font-weight: 600; font-size: 25px; line-height: 38px;
  }
  .contact-list svg { width: 22px; height: 22px; flex: none; }
  .footer-band {
    position: absolute; left: 0; right: 0; bottom: 0; height: 54px;
    background: var(--band);
    display: flex; align-items: center; justify-content: flex-end;
    padding-right: 42px;
  }
  .website {
    font-weight: 600; font-size: 23px; color: var(--band-text);
  }
</style>
</head>
<body>
  <div class="business-card">
    <div class="brand-lockup">
      <div class="brand-square"></div>
      <div class="brand-name">Cedar Ridge<br>Mechanical</div>
    </div>

    <div class="divider"></div>

    <div class="contact-block">
      <h1 class="person-name">DANIEL HARPER</h1>
      <p class="person-title">Managing Director</p>
      <p class="address">Your address, City<br>State, Zip 1234</p>
      <ul class="contact-list">
        <li>
          <svg viewBox="0 0 24 24" fill="var(--ink)"><path d="M6.6 10.8a15.1 15.1 0 0 0 6.6 6.6l2.2-2.2a1 1 0 0 1 1-.25 11.4 11.4 0 0 0 3.6.57 1 1 0 0 1 1 1V20a1 1 0 0 1-1 1A17 17 0 0 1 3 4a1 1 0 0 1 1-1h3.5a1 1 0 0 1 1 1c0 1.25.2 2.45.57 3.57a1 1 0 0 1-.25 1z"/></svg>
          123 456 789
        </li>
        <li>
          <svg viewBox="0 0 24 24" fill="none" stroke="var(--ink)" stroke-width="2.2"><rect x="6" y="2" width="12" height="20" rx="2"/><line x1="10" y1="18" x2="14" y2="18"/></svg>
          123 456 789
        </li>
        <li>
          <svg viewBox="0 0 24 24" fill="none" stroke="var(--ink)" stroke-width="2.2"><rect x="2" y="5" width="20" height="15" rx="2"/><path d="M2 6l10 8 10-8"/></svg>
          info@yourgmail.com
        </li>
      </ul>
    </div>

    <div class="footer-band">
      <p class="website">www.yourwebsite.com</p>
    </div>
  </div>
</body>
</html>
```